Request for Business Card Design

Hi. My name is Marlene, I am looking for a new business card design for my company, Quarrow Signal Instruments, LLC. I really like the design you did for Tarsel Venture and was hoping you could do something similar using our full logo and our mark. I am also open to any raised texture design using our mark. I have attached our full logo, which would need to be somewhere on the card, as well as the mark in both outline and full form, as well as our brand colors / guide. The card does not have to be white, as long as our logo and mark appear. I actually like darker colored business cards more, but am open to all options. If you are interested in working with me, please let me know. We would also take the business card design into letterhead design if you can do that.

```html
<!DOCTYPE html>
<html lang="en">
<head>
<meta charset="utf-8">
<title>Quarrow Signal Instruments – Business Card</title>
<link href="https://fonts.googleapis.com/css2?family=Titillium+Web:wght@400;600;700&display=swap" rel="stylesheet">
<style>
  :root {
    --backdrop: #7e9bc1;
    --card-dark: #2a2829;
    --card-dark-edge: #1e1c1d;
    --brand-green: #7cc142;
    --brand-green-deep: #69b533;
    --brand-blue: #2ea3cf;
    --text-light: #ffffff;
    --text-muted: #cfcfcf;
    --text-faint: #6f6d6e;
    --divider: #8a8676;
  }
  html, body {
    margin: 0;
    padding: 0;
    width: 1200px;
    height: 876px;
    overflow: hidden;
    background: var(--backdrop);
    font-family: "Titillium Web", sans-serif;
  }
  .canvas {
    position: relative;
    width: 1200px;
    height: 876px;
  }
  .card {
    position: absolute;
    width: 530px;
    height: 303px;
    border-radius: 3px;
    box-shadow: 0 14px 30px rgba(20, 35, 70, 0.35);
    overflow: hidden;
  }
  .card--front { left: 45px; top: 330px; background: var(--card-dark); }
  .card--back {
    left: 625px; top: 200px;
    background: linear-gradient(135deg, var(--brand-green) 0%, var(--brand-green-deep) 100%);
  }
  .card svg { display: block; width: 100%; height: 100%; }
  .logo-name { font-weight: 700; letter-spacing: 2px; fill: var(--text-light); }
  .logo-tagline { font-weight: 600; letter-spacing: 1px; fill: var(--text-light); }
  .person-name { font-weight: 700; fill: var(--text-light); letter-spacing: 0.5px; }
  .person-role { font-weight: 400; fill: var(--text-muted); }
  .contact-line { font-weight: 400; fill: var(--text-light); font-size: 12px; }
  .website { font-weight: 400; fill: var(--text-faint); font-size: 11px; letter-spacing: 5px; }
  .icon-dot { fill: var(--brand-green); }
  .icon-glyph { fill: none; stroke: var(--card-dark); stroke-width: 1.4; stroke-linecap: round; stroke-linejoin: round; }
</style>
</head>
<body>
<main class="canvas">

  <section class="card card--front" aria-label="Business card front">
    <svg viewBox="0 0 530 303" xmlns="http://www.w3.org/2000/svg">
      <path class="swoosh swoosh--green" fill="var(--brand-green)"
            d="M0,0 L46,0 C130,62 230,122 340,172 C225,135 105,78 0,34 Z"/>
      <path class="swoosh swoosh--blue" fill="var(--brand-blue)"
            d="M48,82 C160,160 330,200 530,204 L530,228 C330,222 165,178 48,82 Z"/>

      <g class="brand-lockup">
        <circle cx="300" cy="62" r="13" fill="none" stroke="var(--text-light)" stroke-width="4"/>
        <text class="logo-name" x="322" y="73" font-size="30">QUARROW</text>
        <text class="logo-tagline" x="323" y="88" font-size="8.5">SIGNAL INSTRUMENTS</text>
      </g>

      <g class="identity">
        <text class="person-name" x="140" y="246" font-size="17" text-anchor="end">MARLENE</text>
        <text class="person-role" x="140" y="262" font-size="11" text-anchor="end">Director</text>
      </g>
      <line class="divider" x1="155" y1="228" x2="155" y2="282" stroke="var(--divider)" stroke-width="1"/>

      <g class="contacts">
        <circle class="icon-dot" cx="174" cy="238" r="7"/>
        <rect class="icon-glyph" x="171.5" y="234" width="5" height="8" rx="1"/>
        <text class="contact-line" x="188" y="242">+000 12345 6789</text>

        <circle class="icon-dot" cx="174" cy="256" r="7"/>
        <rect class="icon-glyph" x="170" y="253" width="8" height="6"/>
        <path class="icon-glyph" d="M170,253 L174,256.5 L178,253"/>
        <text class="contact-line" x="188" y="260">urname@email.com</text>

        <circle class="icon-dot" cx="174" cy="274" r="7"/>
        <path class="icon-glyph" d="M174,279 C171,275 171,273 171,272 A3,3 0 0 1 177,272 C177,273 177,275 174,279 Z"/>
        <text class="contact-line" x="188" y="278">Street Address Here</text>
        <text class="contact-line" x="188" y="293">Singapore, 2222</text>
      </g>

      <text class="website" x="20" y="22" transform="rotate(90 20 22)">www.quarrowsignal.com</text>
    </svg>
  </section>

  <section class="card card--back" aria-label="Business card back">
    <svg viewBox="0 0 530 303" xmlns="http://www.w3.org/2000/svg">
      <g class="brand-lockup">
        <circle cx="90" cy="128" r="20" fill="none" stroke="var(--text-light)" stroke-width="6"/>
        <text class="logo-name" x="124" y="146" font-size="44">QUARROW</text>
        <text class="logo-tagline" x="126" y="166" font-size="12">SIGNAL INSTRUMENTS</text>
      </g>
    </svg>
  </section>

</main>
</body>
</html>
```